Buchcover-Design für Roman
Zielgruppe
Ich bin Autor und veröffentliche meinen ersten Roman.
Eine humoristische Geschichte voller Musik und Filmzitate.
Die Zielgruppe sind Erwachsene zwischen 30 und 40.
Aufgabenstellung
Titel: Die Welt dreht sich halt im Kreis
Autor: Tobias Hellenkamp
Bitte unbedingt auch die technischen Vorgaben beachten, siehe auch die Musterdatei, die ich hochgeladen habe.(Cover.PNG)
Technische Daten des Verlages:
Das Buch soll als Paperback und als Ebook gleichzeitig im KRU-Verlag erscheinen.
Das Paperback soll das Format 12 * 19 cm haben, also jeweils die Vorderseite und Rückseite.
Es werden ca. 380 Seiten dabei herauskommen.
Ich gehe von ca. 2,5 cm für den Buchrücken aus.
Laut Verlag muss die Farbdatei mindestens 300 dpi haben.
Das Format beträgt laut KRU: 275,1 mm * 200,0 mm .
Zusätzlich muss auf die Rückseite ein Barcode als PNG Datei eingefügt werden, der 144 dpi haben wird.
Vorläufiger Klappentext:
Markus Finkler, für seine Freunde, wenn er denn noch welche hätte, einfach nur Finki, ist ein nerdiger Verlierertyp, der in eine tiefe Sinnkrise stürzt. Verantwortlich dafür sind 3 Dinge, sein nahender 40. Geburtstag, der Tod seines Vaters und die Einladung zum Klassentreffen seiner alten Schule. Bisher hat er in seinem Leben noch nicht viel hinbekommen und sich auch deshalb von den Menschen entfernt. Er führt ein einsames Dasein, in seiner begrenzten Welt aus Filmen und Musik. Nun, auch mit 39 noch lange nicht erwachsen, muss er sich diesen Dingen stellen und sein Leben endlich auf die Reihe bekommen, wobei er natürlich von einer Katastrophe in die nächste stürzt.
Vorläufige Autoreninfo:
Der Autor wurde 1979 in Dortmund geboren und lebt seit 2017 mit seiner Familie in seiner Wahlheimat, dem beschaulichen Kempen am Niederrhein. Er ist hauptberuflich bei einem großen Finanzdienstleistungsunternehmen in Düsseldorf tätig, verwirklichte sich zu seinem 40. Geburtstag seinen lang gehegten Traum und begann nebenberuflich zu schreiben. Das hier vorliegende Produkt seiner Phantasie stellt seinen 1. Roman dar. Weitere sind in Planung.
Soll beides auf die Rückseite gedruck..

```html
<!DOCTYPE html>
<html lang="de">
<head>
<meta charset="utf-8">
<title>Die Welt dreht sich halt im Kreis – Buchcover</title>
<link rel="stylesheet" href="https://fonts.googleapis.com/css2?family=Bebas+Neue&family=Cinzel:wght@500&family=Open+Sans:wght@400;700&display=swap">
<style>
  :root {
    --stage: #e4e4e4;
    --cover-yellow: #f0a30a;
    --ink: #111111;
    --paper: #ffffff;
    --spine-text: #f3ead6;
    --heading-yellow: #f0a30a;
  }
  * { margin: 0; padding: 0; box-sizing: border-box; }
  html, body {
    width: 1200px;
    height: 3178px;
    overflow: hidden;
    background: var(--stage);
  }
  .stage {
    position: relative;
    width: 1200px;
    height: 3178px;
  }
  .front-cover-large {
    position: absolute;
    left: 100px;
    top: 240px;
    width: 1000px;
    height: 1583px;
    box-shadow: 0 18px 40px rgba(0,0,0,0.18);
  }
  .front-cover-large svg, .wrap-front svg { display: block; width: 100%; height: 100%; }

  .cover-wrap {
    position: absolute;
    left: 50px;
    top: 2063px;
    width: 1100px;
    height: 788px;
    display: flex;
    box-shadow: 0 18px 40px rgba(0,0,0,0.18);
  }
  .wrap-back {
    position: relative;
    width: 498px;
    height: 100%;
    background: var(--ink);
    color: var(--paper);
    font-family: "Open Sans", sans-serif;
    padding: 40px 42px 0 38px;
    overflow: hidden;
  }
  .blurb-heading {
    font-size: 12px;
    font-weight: 700;
    color: var(--heading-yellow);
    letter-spacing: 0.02em;
    margin-bottom: 6px;
  }
  .blurb-text {
    font-size: 11px;
    line-height: 1.45;
    margin-bottom: 16px;
  }
  .back-artwork {
    position: absolute;
    left: 0;
    right: 0;
    bottom: 0;
    height: 330px;
    background:
      radial-gradient(ellipse at 65% 35%, rgba(238,150,40,0.85) 0%, rgba(150,70,20,0.55) 30%, rgba(17,17,17,0) 65%),
      radial-gradient(ellipse at 22% 60%, rgba(120,120,170,0.6) 0%, rgba(17,17,17,0) 40%),
      linear-gradient(180deg, #111111 0%, #2a1c14 60%, #1a1410 100%);
  }
  .back-footer {
    position: absolute;
    right: 26px;
    bottom: 22px;
    display: flex;
    align-items: flex-end;
    gap: 10px;
  }
  .barcode-area {
    width: 120px;
    height: 48px;
    background: var(--paper);
  }
  .publisher-mark {
    display: flex;
    align-items: center;
    gap: 6px;
    font-family: "Open Sans", sans-serif;
    font-weight: 700;
    font-size: 15px;
    color: var(--paper);
  }
  .publisher-mark .mark-square {
    width: 14px;
    height: 14px;
    background: var(--paper);
  }
  .wrap-spine {
    width: 104px;
    height: 100%;
    background: var(--ink);
    display: flex;
    flex-direction: column;
    justify-content: space-between;
    align-items: center;
    padding: 30px 0;
    writing-mode: vertical-rl;
    transform: rotate(180deg);
    font-family: "Cinzel", serif;
    color: var(--spine-text);
  }
  .spine-title { font-size: 24px; letter-spacing: 0.02em; white-space: nowrap; }
  .spine-author { font-size: 17px; white-space: nowrap; }
  .wrap-front { width: 498px; height: 100%; }
</style>
</head>
<body>
<svg width="0" height="0" style="position:absolute" aria-hidden="true">
  <defs>
    <linearGradient id="figure-tone" x1="0" y1="0" x2="0" y2="1">
      <stop offset="0" stop-color="#111111" stop-opacity="0.7"/>
      <stop offset="1" stop-color="#111111" stop-opacity="0.35"/>
    </linearGradient>
    <symbol id="front-cover" viewBox="0 0 1200 1900">
      <rect class="cover-ground" width="1200" height="1900" fill="#f0a30a"/>
      <g class="cover-title" font-family="'Bebas Neue', sans-serif" fill="#111111" text-anchor="end">
        <text x="1110" y="330" font-size="120">DIE WELT</text>
        <text x="1110" y="500" font-size="150">DREHT SICH HALT</text>
        <text x="1110" y="730" font-size="240">IM KREIS</text>
      </g>
      <rect class="cover-figure" x="110" y="770" width="620" height="1050" rx="40" fill="url(#figure-tone)" role="img" aria-label="Illustration: schlanke Strichfigur mit Sonnenbrille, die eine Filmrolle hält"/>
      <rect class="author-band" x="520" y="1460" width="760" height="130" rx="65" fill="#111111"/>
      <text class="author-name" x="1150" y="1545" text-anchor="end" font-family="'Cinzel', serif" font-size="58" fill="#ffffff">TOBIAS HELLENKAMP</text>
    </symbol>
  </defs>
</svg>

<main class="stage">
  <section class="front-cover-large">
    <svg viewBox="0 0 1200 1900" role="img" aria-label="Vorderseite: Die Welt dreht sich halt im Kreis, Tobias Hellenkamp"><use href="#front-cover"/></svg>
  </section>

  <section class="cover-wrap">
    <div class="wrap-back">
      <h2 class="blurb-heading">DAS BUCH:</h2>
      <p class="blurb-text">Markus Finkler, für seine Freunde, wenn er denn noch welche hätte, einfach nur Finki, ist ein nerdiger Verlierertyp, der in eine tiefe Sinnkrise stürzt. Verantwortlich dafür sind 3 Dinge, sein nahender 40. Geburtstag, der Tod seines Vaters und die Einladung zum Klassentreffen seiner alten Schule. Bisher hat er in seinem Leben noch nicht viel hinbekommen und sich auch deshalb von den Menschen entfernt. Er führt ein einsames Dasein, in seiner begrenzten Welt aus Filmen und Musik. Nun, auch mit 39 noch lange nicht erwachsen, muss er sich diesen Dingen stellen und sein Leben endlich auf die Reihe bekommen, wobei er natürlich von einer Katastrophe in die nächste stürzt.</p>
      <h2 class="blurb-heading">DER AUTOR:</h2>
      <p class="blurb-text">Der Autor wurde 1979 in Dortmund geboren und lebt seit 2017 mit seiner Familie in seiner Wahlheimat, dem beschaulichen Kempen am Niederrhein. Er ist hauptberuflich bei einem großen Finanzdienstleistungsunternehmen in Düsseldorf tätig, verwirklichte sich zu seinem 40. Geburtstag seinen lang gehegten Traum und begann nebenberuflich zu schreiben. Das hier vorliegende Produkt seiner Phantasie stellt seinen 1. Roman dar. Weitere sind in Planung.</p>
      <div class="back-artwork" role="img" aria-label="Foto: Filmrolle vor dunklem Hintergrund mit orangefarbenem Lichtschein"></div>
      <div class="back-footer">
        <div class="barcode-area" role="img" aria-label="Freifläche für den Barcode des Verlags"></div>
        <div class="publisher-mark"><span class="mark-square"></span>KRU</div>
      </div>
    </div>
    <div class="wrap-spine">
      <span class="spine-author">TOBIAS HELLENKAMP</span>
      <span class="spine-title">DIE WELT DREHT SICH HALT IM KREIS</span>
    </div>
    <div class="wrap-front">
      <svg viewBox="0 0 1200 1900" role="img" aria-label="Vorderseite im Umschlag"><use href="#front-cover"/></svg>
    </div>
  </section>
</main>
</body>
</html>
```